Website creation for audiovisual activities

I want a website for my director of photography activity. It's primarily composed of screenshots in gallery format, followed by detailed pages for each production.

Here's my current website:
www.lionelbaquet.com
I'd like a more modern and streamlined design, and for the site to be responsive on phones and computers. I also want to be able to easily add photos and text to it later.

Target Market(s)

productions society, directors and producers.

Industry/Entity Type

Audiovisual / TV

Coding

Coded - Design and coding required

Number of Pages Required

5+ page

Font styles to use
Sans Serif

Colors
0054AA
0677BA
7BADD7
CADEEF
E8F1F8
0094D4
00A9DD
6FCCEA
C7EBF8
E9F6FB
00AB8E
00BBA5
67D7C9
C6EFE9
E9F9F6
6B429C
8869AF
B7A5CE
E3DAEB
F3F0F8

Requirements
Must have
• a modern look with a photo gallery on the homepage
Nice to have
• a light background with large, dynamic images
Should not have
• a dark background and an overly classic look

```html
<!DOCTYPE html>
<html lang="en">
<head>
<meta charset="utf-8">
<title>Lionel Baquet – Director of Photography</title>
<link rel="stylesheet" href="https://fonts.googleapis.com/css2?family=Cinzel:wght@400;500&family=Montserrat:wght@400;500;600&display=swap">
<style>
:root{
  --blue-deep:#0054AA;
  --blue:#0677BA;
  --blue-bright:#0094D4;
  --blue-soft:#7BADD7;
  --ink:#2b2f36;
  --text:#5a6270;
  --rule:#CADEEF;
  --bg:#ffffff;
  --footer:#14161c;
  --footer-base:#0c0d11;
  --footer-text:#c9ced8;
}
*{margin:0;padding:0;box-sizing:border-box}
html,body{width:1200px;height:3800px;overflow:hidden;background:var(--bg)}
body{font-family:"Montserrat",sans-serif;color:var(--text);position:relative}
.header{position:absolute;top:0;left:0;width:1200px;height:80px;display:flex;align-items:center;justify-content:space-between;padding:0 110px;border-bottom:1px solid #eef2f6}
.brand{line-height:1}
.brand-name{font-family:"Montserrat",sans-serif;font-weight:500;font-size:26px;letter-spacing:1px;color:var(--ink)}
.brand-role{font-family:"Montserrat",sans-serif;font-size:17px;color:var(--ink);margin-top:4px}
.nav{display:flex;gap:34px}
.nav a{font-family:"Cinzel",serif;font-size:15px;color:var(--ink);text-decoration:none;letter-spacing:.5px;padding-bottom:6px}
.nav a.is-active{color:var(--blue-bright);border-bottom:2px solid var(--blue-bright)}
.hero-title{position:absolute;top:118px;left:0;width:1200px;text-align:center;font-family:"Cinzel",serif;font-size:32px;line-height:44px;color:var(--ink)}
.photo{position:absolute;border-radius:2px}
.photo-hero{top:365px;left:110px;width:980px;height:530px;background:linear-gradient(135deg,#3a0d10,#b81c22 45%,#2a2c33)}
.photo-set{top:1300px;left:110px;width:980px;height:540px;background:linear-gradient(160deg,#3a2a1e,#6b4a2e 50%,#1d1b1c)}
.section-title{position:absolute;left:0;width:1200px;text-align:center;font-family:"Cinzel",serif;font-size:32px;color:var(--ink)}
.section-title::after{content:"";display:block;width:340px;height:2px;background:var(--blue-soft);margin:14px auto 0}
.copy{position:absolute;left:110px;width:980px;font-size:15px;line-height:26px}
.copy p+p{margin-top:22px}
.gallery{position:absolute;top:2190px;left:110px;width:980px;display:grid;grid-template-columns:470px 470px;gap:40px;row-gap:30px}
.gallery .tile{height:280px;border-radius:2px}
.tile-1{background:linear-gradient(135deg,#3b2a6b,#c9359a 55%,#1c1f4a)}
.tile-2{background:radial-gradient(circle at 45% 45%,#f4d8e8,#b3226d 30%,#1a0c18 75%)}
.tile-3{background:linear-gradient(150deg,#1c2a7a,#c42a6c 55%,#2a1040)}
.tile-4{background:radial-gradient(circle at 60% 50%,#ff6b5a,#b0161c 40%,#2a0508 80%)}
.button{position:absolute;left:50%;transform:translateX(-50%);background:var(--blue);color:#fff;font-size:13px;font-weight:500;letter-spacing:1px;padding:14px 30px;text-transform:uppercase;white-space:nowrap}
.footer{position:absolute;top:3395px;left:0;width:1200px;height:365px;background:var(--footer);color:var(--footer-text)}
.footer .brand{position:absolute;top:70px;left:110px}
.footer .brand-name,.footer .brand-role{color:#fff}
.social{position:absolute;top:170px;left:110px;display:flex;gap:12px}
.social span{width:26px;height:26px;border-radius:50%;background:var(--blue-bright)}
.footer-nav{position:absolute;top:70px;left:510px;list-style:none}
.footer-nav li,.contact li{font-family:"Cinzel",serif;font-size:15px;line-height:36px;display:flex;align-items:center;gap:16px}
.footer-nav li::before,.contact li::before{content:"";width:8px;height:8px;border-radius:50%;background:var(--blue-bright)}
.contact{position:absolute;top:70px;left:845px;list-style:none}
.contact li{font-size:13px;line-height:40px}
.footer-button{position:absolute;top:180px;left:845px;background:var(--blue);color:#fff;font-size:13px;letter-spacing:1px;padding:14px 28px}
.footer-base{position:absolute;top:3760px;left:0;width:1200px;height:40px;background:var(--footer-base);color:var(--footer-text);font-family:"Cinzel",serif;font-size:13px;display:flex;align-items:center;justify-content:center}
</style>
</head>
<body>
<header class="header">
  <div class="brand">
    <div class="brand-name">LIONEL BAQUET</div>
    <div class="brand-role">Directeur Photo</div>
  </div>
  <nav class="nav">
    <a class="is-active" href="#">Presentation</a>
    <a href="#">Magazine</a>
    <a href="#">Show</a>
    <a href="#">Fiction / Event</a>
    <a href="#">Talk Info</a>
  </nav>
</header>

<h1 class="hero-title">Lionel Baquet<br>Director of Photography<br>Crafting visual narratives for television and film.</h1>

<div class="photo photo-hero" role="img" aria-label="Television talk show studio with guests seated around a table under red lighting"></div>

<h2 class="section-title" style="top:985px">About us</h2>
<div class="copy" style="top:1075px">
  <p>We create visually compelling narratives for television and film productions. With a strong focus on composition, lighting, and movement, each project is approached with precision and creative sensitivity. From large-scale productions to intimate storytelling formats, our work is defined by clarity, atmosphere, and visual impact. We create visually compelling narratives for television and film productions. With a strong focus on composition, lighting, and movement, each project is approached with precision and creative sensitivity. From large-scale productions to intimate storytelling formats, our work is defined by clarity, atmosphere, and visual impact.</p>
</div>

<div class="photo photo-set" role="img" aria-label="Warmly lit television set with a chalkboard sign and a dining table"></div>

<h2 class="section-title" style="top:1955px">A collection of visual moments captured on set.</h2>
<div class="copy" style="top:2060px">
  <p>We create visually compelling narratives for television and film productions. With a strong focus on composition, lighting, and movement, each project is approached with precision and creative sensitivity. From large-scale productions to intimate storytelling formats, our work is defined by clarity, atmosphere, and visual impact.</p>
</div>

<div class="gallery">
  <div class="tile tile-1" role="img" aria-label="Concert stage with audience under purple and pink lights"></div>
  <div class="tile tile-2" role="img" aria-label="Stage light beams bursting over a performance"></div>
  <div class="tile tile-3" role="img" aria-label="Dancers on a stage lit in blue and magenta"></div>
  <div class="tile tile-4" role="img" aria-label="Performer on a red lit stage"></div>
</div>

<div class="button" style="top:2830px">View more gallery</div>

<h2 class="section-title" style="top:2965px">About Lionel Baquet</h2>
<div class="copy" style="top:3065px">
  <p>I am a Director of Photography working in television production, focused on translating narrative concepts into precise visual language. My work combines structured composition, naturalistic lighting, and controlled camera movement to create atmosphere without overpowering the story.</p>
  <p>I collaborate closely with directors and creative teams to shape a cohesive visual identity for each production. Based in [Location], available for national and international projects.</p>
</div>

<div class="button" style="top:3255px">Read more about me</div>

<footer class="footer">
  <div class="brand">
    <div class="brand-name">LIONEL BAQUET</div>
    <div class="brand-role">Directeur Photo</div>
  </div>
  <div class="social"><span></span><span></span><span></span></div>
  <ul class="footer-nav">
    <li>Presentation</li>
    <li>Magazine</li>
    <li>Show</li>
    <li>Fiction / Event</li>
    <li>Talk Info</li>
  </ul>
  <ul class="contact">
    <li>Phone 0612345678</li>
    <li>Email: contact@lionelbaquet.com</li>
  </ul>
  <div class="footer-button">NEWSLETTER</div>
</footer>
<div class="footer-base">© 2026 Lionel Baquet</div>
</body>
</html>
```